Business Card Design Project

We are a construction company in Orange County, CA. We need a two sided business card. We would like the back to be our logo with web URL. Front should included Name, title, address, phone, fax and email address.

our address is
627 West Dorrance Blvd, Suite 308
Anaheim, CA 92718

Our logo files are attached.

Construction

```html
<!DOCTYPE html>
<html lang="en">
<head>
<meta charset="utf-8">
<title>Varden Business Card</title>
<link href="https://fonts.googleapis.com/css2?family=Open+Sans:wght@400;700&display=swap" rel="stylesheet">
<style>
  :root {
    --stage: #ece6df;
    --card: #ffffff;
    --card-edge: #5a5a5a;
    --brand: #184a7e;
    --ink: #444444;
    --muted: #555555;
  }
  * { box-sizing: border-box; margin: 0; padding: 0; }
  html, body { width: 1200px; height: 1044px; overflow: hidden; }
  body {
    background: var(--stage);
    font-family: "Open Sans", Arial, sans-serif;
    position: relative;
  }
  .card {
    position: absolute;
    background: var(--card);
    border: 1px solid var(--card-edge);
    border-radius: 23px;
  }
  .card--front { left: 66px; top: 69px; width: 751px; height: 429px; }
  .card--back { left: 366px; top: 537px; width: 750px; height: 427px; }

  .brand-name {
    position: absolute;
    font-weight: 700;
    color: var(--brand);
    font-size: 100px;
    line-height: 1;
    letter-spacing: -2px;
    white-space: nowrap;
  }
  .card--front .brand-name { left: 46px; top: 42px; }
  .card--back .brand-name { left: 0; right: 0; text-align: center; top: 135px; }

  .contact-list {
    position: absolute;
    left: 48px; top: 211px;
    list-style: none;
    font-size: 18.5px;
    color: var(--ink);
    line-height: 24px;
  }
  .contact-list li { display: flex; align-items: center; gap: 7px; }
  .contact-list svg { width: 15px; height: 15px; fill: var(--ink); flex: none; }

  .address {
    position: absolute;
    left: 48px; top: 335px;
    font-size: 18.5px;
    color: var(--ink);
    line-height: 24px;
    font-style: normal;
  }
  .person {
    position: absolute;
    right: 50px; top: 210px;
    text-align: right;
    color: var(--brand);
  }
  .person-name { font-size: 26px; font-weight: 700; line-height: 34px; }
  .person-title { font-size: 23px; font-weight: 400; line-height: 32px; }

  .web-url {
    position: absolute;
    left: 0; right: 0; top: 288px;
    text-align: center;
    font-size: 19px;
    letter-spacing: 4px;
    color: var(--muted);
  }
</style>
</head>
<body>
  <section class="card card--front" aria-label="Card front">
    <div class="brand-name">VARDEN</div>

    <ul class="contact-list">
      <li>
        <svg viewBox="0 0 16 16" aria-label="Phone"><path d="M4 1.5l2.3 3-1.4 1.6c.8 1.8 2.2 3.2 4 4l1.6-1.4 3 2.3-1.3 2.5C7 13.8 2.2 9 1.5 2.8z"/></svg>
        <span>01-555-0142</span>
      </li>
      <li>
        <svg viewBox="0 0 16 16" aria-label="Fax"><path d="M4 2h6l2 2v3H4zM2 7h12v6H2zm2 2v2h8V9z"/></svg>
        <span>01-555-0143</span>
      </li>
      <li>
        <svg viewBox="0 0 16 16" aria-label="Email"><path d="M1 4h14v9H1zm1 1l6 4 6-4z"/></svg>
        <span>info@vardenbuild.com</span>
      </li>
      <li>
        <svg viewBox="0 0 16 16" aria-label="Website"><circle cx="8" cy="8" r="6.5"/></svg>
        <span>www.vardenbuild.com</span>
      </li>
    </ul>

    <address class="address">
      627 West Dorrance Blvd<br>
      Suite 308, Anaheim, CA&nbsp;&nbsp;92718
    </address>

    <div class="person">
      <div class="person-name">Your Name</div>
      <div class="person-title">Title</div>
    </div>
  </section>

  <section class="card card--back" aria-label="Card back">
    <div class="brand-name">VARDEN</div>
    <div class="web-url">www.vardenbuild.com</div>
  </section>
</body>
</html>
```